Brimlow OrthoLink IT Inc. new website

i need a website for my company which is dedicated to installation and service of computer systems in Dental Offices. I would like for it to encompass a technology feel and professional look. The company deals with all aspects of technology like, Audio Visual, computer systems and networks, Cloud services like data backup, data center. We provide manage services, support and services to Dental Professionals.
Updates

Looking for a Technology font but professional look Added Wednesday, April 20, 2016

Target Market(s)

Dental, Dentist

Industry/Entity Type

Dental

Number of Pages Required

5+ page

Font styles to use
Other font styles liked:
• Futuristic or Techy

Colors
0255a3
ec1f27

Requirements
Must have
• Tabs
Nice to have
• Have no idea maybe some suggestion on your part may help
Should not have
• A professional feel but have a techy look

```html
<!DOCTYPE html>
<html lang="en">
<head>
<meta charset="utf-8">
<title>Brimlow OrthoLink IT Inc.</title>
<link href="https://fonts.googleapis.com/css2?family=Roboto+Condensed:wght@400;700&family=Open+Sans:wght@400;600;700&family=Raleway:wght@400;500&family=Lato:wght@700;900&display=swap" rel="stylesheet">
<style>
:root{
  --brand:#0255a3;
  --brand-dark:#0a4a8c;
  --accent:#ec1f27;
  --ink:#111;
  --text:#555;
  --light:#fff;
  --grey-band:#ebebeb;
  --dark-band:#1d1d1f;
  --footer:#111;
}
*{margin:0;padding:0;box-sizing:border-box}
html,body{width:1200px;height:2862px;overflow:hidden}
body{position:relative;background:#fff;font-family:'Open Sans',sans-serif;color:var(--text)}
section,header,footer{position:absolute;left:0;width:1200px}
.abs{position:absolute}

/* header */
.site-header{top:0;height:109px;background:#fff;border-top:6px solid var(--brand);box-shadow:0 2px 6px rgba(0,0,0,.12);z-index:2}
.brand{left:78px;top:28px;display:flex;align-items:center;gap:12px;font-family:'Roboto Condensed',sans-serif;font-weight:700;font-size:30px;color:var(--brand)}
.brand-mark{width:34px;height:34px;background:var(--brand);border-radius:6px}
.main-nav{left:450px;top:28px;display:flex;align-items:center;font-family:'Roboto Condensed',sans-serif;font-size:18px;color:#444}
.main-nav a{text-decoration:none;color:inherit;padding:0 17px;line-height:46px}
.main-nav a.active{background:var(--brand);color:#fff;border-radius:3px;padding:0 24px;margin-right:2px}

/* hero */
.hero{top:109px;height:492px}
.hero-photo{position:absolute;inset:0;background:linear-gradient(90deg,#f4f6f8 0%,#eef2f6 35%,#d8e0e8 60%,#c9d2dc 100%)}
.hero h1{left:78px;top:92px;font-family:'Lato',sans-serif;font-weight:900;font-size:42px;line-height:58px;color:var(--ink)}
.hero p{left:78px;top:218px;width:480px;font-size:18px;line-height:30px;color:#222}
.btn{display:inline-block;background:var(--brand);color:#fff;font-family:'Roboto Condensed',sans-serif;font-weight:700;text-decoration:none;text-align:center;border-radius:4px}
.hero .btn{left:78px;top:301px;width:201px;height:61px;line-height:61px;font-size:24px}

/* welcome */
.welcome{top:601px;height:389px;background:#fff}
.welcome h2{left:78px;top:62px;width:660px;white-space:nowrap;font-family:'Raleway',sans-serif;font-weight:400;font-size:30px;color:var(--ink);letter-spacing:0}
.welcome h2 span{color:var(--brand)}
.welcome .copy{left:78px;top:118px;width:605px;font-size:15.5px;line-height:25px}
.welcome .copy p+p{margin-top:25px}
.read-more{left:78px;top:306px;font-family:'Lato',sans-serif;font-weight:700;font-size:20px;color:var(--brand);text-decoration:none}
.monitor{left:759px;top:63px;width:363px;height:296px}

/* technology */
.technology{top:990px;height:470px;color:#fff}
.tech-photo{position:absolute;inset:0;background:linear-gradient(90deg,#2b2b2d 0%,#3a3b3d 45%,#2a2a2b 100%)}
.technology h2{left:0;width:1200px;top:44px;text-align:center;font-family:'Raleway',sans-serif;font-weight:400;font-size:38px;letter-spacing:1px}
.tech-item{top:113px;width:330px;text-align:center}
.tech-icon{width:126px;height:126px;border-radius:50%;background:var(--brand);margin:0 auto;display:flex;align-items:center;justify-content:center}
.tech-item h3{font-family:'Raleway',sans-serif;font-weight:500;font-size:21px;line-height:33px;margin-top:16px}
.tech-item p{font-size:15.5px;line-height:25px;margin-top:4px;padding:0 8px}

/* services */
.services{top:1460px;height:238px;background:#fff}
.service{top:47px;display:flex;gap:15px}
.service-photo{width:208px;height:134px;flex:none}
.service h3{font-family:'Roboto Condensed',sans-serif;font-weight:400;font-size:26px;color:var(--brand);margin-top:-2px}
.service p{width:270px;font-size:15.5px;line-height:25px;margin-top:6px}

/* testimonial */
.testimonials{top:1698px;height:372px;background:var(--grey-band)}
.testimonials h2{left:0;width:1200px;top:60px;text-align:center;font-family:'Roboto Condensed',sans-serif;font-weight:400;font-size:40px;color:var(--ink)}
.testimonials h2 span{color:var(--brand)}
.quote-mark{left:576px;top:134px}
.arrow{width:61px;height:61px;border:2px solid #222;border-radius:50%;top:178px}
.testimonials blockquote{left:222px;top:186px;width:756px;text-align:center;font-size:15.5px;line-height:25px;color:#333}
.client-name{left:0;width:1200px;top:290px;text-align:center;font-weight:700;font-size:15px;color:var(--brand)}

/* news */
.news{top:2070px;height:269px;background:#fff}
.news h2{left:0;width:1200px;top:44px;text-align:center;font-family:'Roboto Condensed',sans-serif;font-weight:400;font-size:40px;color:var(--ink)}
.news h2 span{color:var(--brand)}
.news-item{top:126px;display:flex;gap:12px}
.news-date{width:71px;height:80px;background:var(--brand);color:#fff;text-align:center;flex:none}
.news-date b{display:block;font-family:'Roboto Condensed',sans-serif;font-size:32px;line-height:44px;padding-top:4px}
.news-date span{font-size:15px}
.news-item p{width:250px;font-size:14.5px;line-height:25px;color:#555}
.news-item a{display:block;font-weight:700;font-size:13.5px;color:var(--ink);text-decoration:none}

/* contact */
.contact{top:2339px;height:470px;color:#fff}
.contact-photo{position:absolute;inset:0;background:linear-gradient(90deg,#2f67ac 0%,#3a73b6 50%,#2e66a8 100%)}
.divider{left:600px;top:48px;width:2px;height:390px;background:rgba(255,255,255,.45)}
.contact h2{font-family:'Roboto Condensed',sans-serif;font-weight:400;font-size:30px;top:42px}
.field{left:78px;width:393px;height:38px;border:1.5px solid #fff;font-size:15px;padding:8px 10px;color:#fff}
.submit{left:78px;top:374px;width:145px;height:46px;line-height:46px;background:#fff;color:var(--brand);font-family:'Roboto Condensed',sans-serif;font-size:22px;text-align:center}
.info-row{left:655px;display:flex;gap:14px;font-size:15px;line-height:24px}
.info-row svg{flex:none;margin-top:4px}
.social{top:290px;width:62px;height:62px;border-radius:50%}
.social.solid{background:#fff}
.social.ring{border:2px solid #fff}

/* footer */
.site-footer{top:2809px;height:53px;background:var(--footer);color:#ddd;text-align:center;line-height:53px;font-size:15px}
.site-footer b{color:#fff}
</style>
</head>
<body>

<header class="site-header">
  <div class="brand abs"><span class="brand-mark"></span>Brimlow OrthoLink IT</div>
  <nav class="main-nav abs">
    <a class="active" href="#">HOME</a><a href="#">ABOUT</a><a href="#">SERVICES</a><a href="#">SUPPORT</a><a href="#">CLIENT</a><a href="#">BLOG</a><a href="#">CONTACT</a>
  </nav>
</header>

<section class="hero">
  <div class="hero-photo" role="img" aria-label="Bright modern dental treatment room with chair instruments and a wall screen showing a dental x-ray"></div>
  <h1 class="abs">TECHNOLOGY FOR<br>BEST PRACTICE</h1>
  <p class="abs">f you view technology as an expense rather than<br>an investment, you haven't worked with us.</p>
  <a class="btn abs" href="#">CONTACT US</a>
</section>

<section class="welcome">
  <h2 class="abs">WELCOME TO <span>BRIMLOW ORTHOLINK IT</span></h2>
  <div class="copy abs">
    <p>Lorem Ipsum is simply dummy text of the printing and typesetting industry. Lorem Ipsum has been the industry's standard dummy text ever since the 1500s, when an unknown printer took a galley of type and scrambled it to make a type specimen book.</p>
    <p>Lorem Ipsum is simply dummy text of the printing and typesetting industry. Lorem Ipsum has been the industry</p>
  </div>
  <a class="read-more abs" href="#">READ MORE &raquo;</a>
  <svg class="monitor abs" viewBox="0 0 363 296" role="img" aria-label="Desktop monitor showing the company video">
    <rect x="0" y="0" width="363" height="245" rx="10" fill="#1a1a1a"/>
    <rect x="10" y="10" width="343" height="210" fill="#fff"/>
    <rect x="0" y="222" width="363" height="23" fill="#d9d9d9"/>
    <text x="181" y="125" text-anchor="middle" font-family="Roboto Condensed, sans-serif" font-weight="700" font-size="24" fill="#0255a3">Brimlow OrthoLink IT</text>
    <path d="M150 245 L213 245 L220 285 L143 285 Z" fill="#bfbfbf"/>
    <rect x="120" y="283" width="123" height="8" rx="3" fill="#cfcfcf"/>
  </svg>
</section>

<section class="technology">
  <div class="tech-photo" role="img" aria-label="Dimly lit dental office interior"></div>
  <h2 class="abs">OUR TECHNOLOGY</h2>
  <div class="tech-item abs" style="left:72px">
    <div class="tech-icon"><svg width="60" height="60" viewBox="0 0 60 60" fill="none" stroke="#fff" stroke-width="3"><rect x="6" y="10" width="48" height="32" rx="2"/><path d="M30 42v8M20 52h20"/><rect x="20" y="18" width="20" height="14" fill="#fff" stroke="none"/></svg></div>
    <h3>Audio Visual</h3>
    <p>Lorem Ipsum is simply dummy text of the printing and typesetting industry. Lorem Ipsum has been the industry.</p>
  </div>
  <div class="tech-item abs" style="left:436px">
    <div class="tech-icon"><svg width="64" height="60" viewBox="0 0 64 60" fill="none" stroke="#fff" stroke-width="3"><rect x="4" y="20" width="22" height="16" rx="2"/><rect x="40" y="6" width="18" height="10"/><rect x="40" y="25" width="18" height="10"/><rect x="40" y="44" width="18" height="10"/><path d="M26 28h7M33 11v38M33 11h7M33 30h7M33 49h7"/></svg></div>
    <h3>Computer Systems and<br>Networks</h3>
    <p>Lorem Ipsum is simply dummy text of the printing and typesetting industry. Lorem Ipsum has been the industry.</p>
  </div>
  <div class="tech-item abs" style="left:802px">
    <div class="tech-icon"><svg width="66" height="60" viewBox="0 0 66 60" fill="none" stroke="#fff" stroke-width="3"><path d="M16 42a12 12 0 0 1 2-24 16 16 0 0 1 30 2 11 11 0 0 1 2 22z"/><ellipse cx="40" cy="40" rx="10" ry="4"/><path d="M30 40v10c0 2 4 4 10 4s10-2 10-4V40M30 45c0 2 4 4 10 4s10-2 10-4"/></svg></div>
    <h3>Cloud Services of Data<br>Backup</h3>
    <p>Lorem Ipsum is simply dummy text of the printing and typesetting industry. Lorem Ipsum has been the industry.</p>
  </div>
</section>

<section class="services">
  <article class="service abs" style="left:78px">
    <div class="service-photo" role="img" aria-label="Business team reviewing documents at a desk" style="background:linear-gradient(135deg,#8fa6bd,#4f5e70)"></div>
    <div><h3>Manage services</h3><p>Lorem Ipsum is simply dummy text of the printing and typesetting industry. Lorem Ipsum has been the industry.</p></div>
  </article>
  <article class="service abs" style="left:637px">
    <div class="service-photo" role="img" aria-label="Support staff wearing headsets" style="background:linear-gradient(135deg,#dfe7ef,#a9b6c4)"></div>
    <div><h3>Support</h3><p>Lorem Ipsum is simply dummy text of the printing and typesetting industry. Lorem Ipsum has been the industry.</p></div>
  </article>
</section>

<section class="testimonials">
  <h2 class="abs">What Our <span>Client Say</span></h2>
  <svg class="quote-mark abs" width="48" height="36" viewBox="0 0 48 36" fill="#666"><path d="M0 36V20C0 8 6 2 18 0v7C11 9 9 13 9 18h9v18zM26 36V20C26 8 32 2 44 0v7c-7 2-9 6-9 11h9v18z"/></svg>
  <svg class="arrow abs" style="left:78px" viewBox="0 0 61 61"><path d="M35 18 L24 30.5 L35 43" fill="none" stroke="#222" stroke-width="2"/></svg>
  <svg class="arrow abs" style="left:1058px" viewBox="0 0 61 61"><path d="M26 18 L37 30.5 L26 43" fill="none" stroke="#222" stroke-width="2"/></svg>
  <blockquote class="abs">Lorem Ipsum is simply dummy text of the printing and typesetting industry. Lorem Ipsum has been the industry's standard dummy text ever since the 1500.Lorem Ipsum is simply dummy text of the printing and typesetting industry.</blockquote>
  <div class="client-name abs">- Client Name</div>
</section>

<section class="news">
  <h2 class="abs">LATEST <span>NEWS</span></h2>
  <article class="news-item abs" style="left:78px"><div class="news-date"><b>21</b><span>Apr</span></div><p>Lorem Ipsum is simply dummy text of the print &amp; typesetting industry.<a href="#">READ MORE</a></p></article>
  <article class="news-item abs" style="left:435px"><div class="news-date"><b>20</b><span>Apr</span></div><p>Lorem Ipsum is simply dummy text of the print &amp; typesetting industry.<a href="#">READ MORE</a></p></article>
  <article class="news-item abs" style="left:800px"><div class="news-date"><b>19</b><span>Apr</span></div><p>Lorem Ipsum is simply dummy text of the print &amp; typesetting industry.<a href="#">READ MORE</a></p></article>
</section>

<section class="contact">
  <div class="contact-photo" role="img" aria-label="Dental office interior under a blue overlay"></div>
  <div class="divider abs"></div>
  <h2 class="abs" style="left:78px">Get In Touch With Us</h2>
  <div class="field abs" style="top:99px">Enter Name</div>
  <div class="field abs" style="top:157px">Enter Email</div>
  <div class="field abs" style="top:214px">Enter Contact No.</div>
  <div class="field abs" style="top:271px;height:80px">Enter Message</div>
  <div class="submit abs">SUBMIT</div>

  <h2 class="abs" style="left:653px">Contact Info</h2>
  <div class="info-row abs" style="top:102px"><svg width="14" height="18" viewBox="0 0 14 18" fill="#fff"><path d="M7 0a7 7 0 0 1 7 7c0 5-7 11-7 11S0 12 0 7a7 7 0 0 1 7-7zm0 4a3 3 0 1 0 0 6 3 3 0 0 0 0-6z"/></svg><span>Lorem Ipsum is simply dummy<br>text of the printing.</span></div>
  <div class="info-row abs" style="top:168px"><svg width="16" height="16" viewBox="0 0 16 16" fill="#fff"><path d="M3 0l3 4-2 2c1 2 3 4 6 6l2-2 4 3-2 3C8 16 0 8 0 2z"/></svg><span>123 456 7890</span></div>
  <div class="info-row abs" style="top:206px"><svg width="16" height="16" viewBox="0 0 16 16" fill="#fff"><rect x="0" y="5" width="16" height="11" rx="1"/><rect x="4" y="0" width="8" height="4" fill="#fff"/></svg><span>123 456 7890</span></div>
  <div class="info-row abs" style="top:248px"><svg width="16" height="12" viewBox="0 0 16 12" fill="none" stroke="#fff" stroke-width="1.6"><rect x="1" y="1" width="14" height="10"/><path d="M1 1l7 6 7-6"/></svg><span>info@brimlowortholink.com</span></div>
  <div class="social solid abs" style="left:650px" aria-label="Social network link"></div>
  <div class="social ring abs" style="left:744px" aria-label="Social network link"></div>
  <div class="social ring abs" style="left:837px" aria-label="Social network link"></div>
</section>

<footer class="site-footer">&copy; <b>BRIMLOW ORTHOLINK IT</b> - 2016. All Rights Reserved.</footer>

</body>
</html>
```